Law Firm Web Design Project

I need a website design for my law firm. I have attached to this description the URL of a website I liked with a description of the elements of that website that appeal to me.

I am also attaching my law firm's logo, so you can review that design when you create the website design.

Reference Site: www.harborfieldcounsel-example.com

What we like about this site:
• The different layers
• Subtle designs, textures, curves
• 3 dimensional
• Floating effect
• Simple logo that stands out (we are providing logo)
• Prominent phone number
• Location of Areas of Practice
oDivorce, Legal Separation, Paternity, Spousal Maintenance, Child Custody, Child Support, Protective Orders, Community Property, Business Evaluations
• The limited amount of links across the top
o Home, Meet Our Attorney, FAQ, Contact Us
• Request A Consultation click through
• Right side bar with the moving icons
• Badges

Other Tips:
• We don’t want the website to be dark. The logo can standout and the website can have its own colors and flow.
• We would like there to be a “call to action” or way to get in touch on every page and every page view
• We would like a place for credit card icons at the bottom of the page
• Strong, yet elegant
• Finally, just use the website provided as a guide. Explore different colors, textures, shapes, shadows etc.
Updates

I would prefer the website have colors that are complementary to my logo and that are strong and elegant.  I like black, gold, amber, and tan colors.  Black should be used sparingly as an accent only, since I don't want the website to be too dark.

Please review the website I provided as an example in my project description.  I really like the three dimensional aspects of that website (web page floating on top of a background and the logo in the upper left floating on top of the web page).  I also like the use of "swirling" on the background and the webpage.  I hope this additional information is helpful.

Requirements
Must have
• I need a place to insert "client testimonials", a place to insert four logos of awards the law firm has received, a place for people to fill out a form to contact the law firm via email, and a place for people to click to review articles I have written.

```html
<!DOCTYPE html>
<html lang="en">
<head>
<meta charset="utf-8">
<title>Whitcombe Law – Divorce and Family Law</title>
<link href="https://fonts.googleapis.com/css2?family=PT+Sans:wght@400;700&family=Source+Sans+3:wght@400;600&display=swap" rel="stylesheet">
<style>
:root{
  --page:#ffffff;
  --backdrop:#f3f3f1;
  --cream:#fdfbf6;
  --gold:#a0802e;
  --brown:#6b4526;
  --brown-dark:#5a3a20;
  --amber:#d9954a;
  --tab-top:#d8a15e;
  --tab-bot:#8e5a2c;
  --text:#2c2c2c;
  --muted:#7a7a7a;
  --rule:#bfa98a;
  --line:#c9c9c9;
}
*{box-sizing:border-box;margin:0;padding:0}
html,body{width:970px;height:1200px;overflow:hidden}
body{background:var(--backdrop);font-family:"PT Sans",sans-serif;color:var(--text);position:relative}
.page{position:absolute;left:61px;top:0;width:848px;height:1200px;background:var(--page);box-shadow:0 0 6px rgba(0,0,0,.15)}
.hero{position:absolute;left:61px;top:0;width:848px;height:315px}
.brand{position:absolute;left:134px;top:10px;display:flex;align-items:center;gap:12px}
.brand-mark{width:48px;height:48px;background:var(--brown-dark)}
.brand-name{font-family:"PT Sans",sans-serif;font-weight:400;font-size:32px;color:var(--gold);letter-spacing:.5px}
.nav{position:absolute;top:6px;left:516px;display:flex;align-items:center;font-family:"Source Sans 3",sans-serif;font-size:13px}
.nav a{color:var(--gold);text-decoration:none;padding:0 22px;border-left:1px solid #ddd;line-height:20px}
.nav a:first-child{border:1px solid #a89867;padding:0 12px;color:#222;font-weight:600;background:linear-gradient(#f6efd9,#cbb98d);border-radius:5px;margin-right:20px}
.nav a:nth-child(2){border-left:0}
.tab{height:45px;border-radius:5px 5px 0 0;background:linear-gradient(var(--tab-top),var(--tab-bot));color:#fff;font-family:"Source Sans 3",sans-serif;font-weight:600;font-size:19px;line-height:45px;box-shadow:0 2px 3px rgba(0,0,0,.3)}
.practice{position:absolute;left:66px;top:333px;width:176px}
.practice .tab{padding-left:20px}
.practice ul{list-style:none;border-left:3px solid var(--brown);background:var(--cream);padding:6px 2px 0 4px;height:650px}
.practice li{font-family:"Source Sans 3",sans-serif;font-weight:600;font-size:12.5px;color:#4a4a4a;height:24.75px;line-height:24px;border-bottom:1px dashed var(--rule);padding-left:17px;position:relative;white-space:nowrap;overflow:hidden}
.practice li::before{content:"›";position:absolute;left:4px;color:#999;font-size:10px}
.main{position:absolute;left:259px;top:335px;width:452px;height:698px;border:1px solid #aaa;border-radius:8px;padding:10px 11px 0 11px}
.main h1{font-family:"Source Sans 3",sans-serif;font-weight:400;font-size:17px;color:var(--brown);margin-bottom:12px}
.main p{font-size:12px;line-height:17.4px;margin-bottom:17.4px}
.more{position:absolute;right:24px;bottom:16px;color:var(--gold);font-size:13px}
.widget{position:absolute;left:729px;width:176px}
.widget .tab{text-align:center}
.widget .body{border:1px solid #bbb;border-top:0;border-radius:0 0 6px 6px;height:110px;padding:10px 8px 0;position:relative;background:#fff}
.widget .row{display:flex;gap:8px}
.icon{width:60px;height:50px;flex:none}
.blurb{font-size:10.5px;line-height:12.5px;color:var(--muted)}
.blurb b{color:var(--brown);display:block}
.click{position:absolute;right:8px;bottom:6px;font-size:11px;font-weight:700;color:var(--brown);border-top:1px solid #ddd;width:160px;text-align:right;padding-top:4px}
.quote{font-size:10.5px;line-height:12.5px;color:var(--muted)}
.author{position:absolute;right:12px;top:52px;font-size:11px;color:var(--muted)}
.arrows{position:absolute;left:8px;right:8px;bottom:4px;border-top:1px solid #ddd;padding-top:2px;text-align:center;font-size:16px;font-weight:700;color:#333;letter-spacing:12px}
.footer{position:absolute;left:61px;top:1047px;width:848px;height:153px;background:linear-gradient(#7a5434,#a87040 50%,#e0a057)}
.copy{position:absolute;left:4px;top:10px;color:#fff;font-size:12px;font-weight:700;line-height:15px}
.pay{position:absolute;left:5px;top:44px;width:200px;height:64px;background:#fff;border-radius:8px;padding:6px 8px}
.pay h3{font-family:"Source Sans 3",sans-serif;font-weight:600;font-size:12px;color:var(--brown);margin-bottom:6px}
.cards{display:flex;gap:4px}
.card{width:43px;height:26px;background:#f1e8da;border:1px solid #c8b79b;font-size:8px;color:var(--brown);display:flex;align-items:center;justify-content:center}
.links{position:absolute;left:238px;top:9px;color:#fff;font-size:12.5px;font-weight:700}
.legal{position:absolute;left:238px;top:32px;width:370px;text-align:center;color:#fff;font-size:7.6px;line-height:12.5px;font-weight:700}
.badges{position:absolute;left:652px;top:13px;width:192px;height:62px;background:#fff;border-radius:6px;display:flex;gap:10px;align-items:center;justify-content:center}
.badge{width:50px;height:46px;background:#ddd6ca;border-radius:4px}
.badge.round{border-radius:50%;width:46px}
</style>
</head>
<body>
<div class="page"></div>

<svg class="hero" viewBox="0 0 848 315" role="img" aria-label="Family of four walking hand in hand toward a lake with a wooden walkway">
  <defs>
    <linearGradient id="scene" x1="0" y1="0" x2="0" y2="1">
      <stop offset="0" stop-color="#e9eff2"/>
      <stop offset=".55" stop-color="#c7d3d4"/>
      <stop offset=".7" stop-color="#6f7a63"/>
      <stop offset="1" stop-color="#8a8576"/>
    </linearGradient>
    <linearGradient id="swirl" x1="0" y1="0" x2="0" y2="1">
      <stop offset="0" stop-color="#ffffff"/>
      <stop offset="1" stop-color="#ececec"/>
    </linearGradient>
  </defs>
  <rect width="848" height="315" fill="url(#scene)"/>
  <path d="M0 0H848V40C700 30 560 40 460 70C380 95 350 150 230 150C140 150 110 110 0 110Z" fill="url(#swirl)"/>
</svg>

<div class="brand"><span class="brand-mark"></span><span class="brand-name">Whitcombe Law</span></div>

<nav class="nav"><a>Home</a><a>Meet Our Attorney</a><a>FAQ</a><a>Contact Us</a></nav>

<aside class="practice">
  <div class="tab">Area of Practice</div>
  <ul>
    <li>Family Law</li><li>Divorce</li><li>Alimony</li><li>Child Custody</li><li>Child Support</li>
    <li>Collaborative Divorce</li><li>Contested Divorce</li><li>Division of Assets</li><li>Domestic Violence</li>
    <li>Family/Relative Adoption</li><li>Fathers’ Rights</li><li>Grandparents’ Rights</li><li>Guardianship</li>
    <li>Legal Separation</li><li>Mediation</li><li>Modification of Spousal</li><li>Mothers’ Rights</li>
    <li>Palimony</li><li>Parental Alienation</li><li>Paternity</li><li>Prenuptial Agreements</li>
    <li>Postnuptial Agreements</li><li>Property Division</li><li>Relocation</li><li>Uncontested Divorce</li><li>Visitation</li>
  </ul>
</aside>

<main class="main">
  <h1>Help with Your Divorce and Family Law Matters</h1>
  <p>Divorce is a difficult and emotional situation, and the outcome could affect the individual and family for years to come. There are many tough decisions and matters to be resolved, including child custody, visitation, spousal support and issues regarding property division. These issues are often hotly contested and may be difficult to resolve amicably. A skilled divorce lawyer from our firm will provide the professional support needed to protect your interests. A Whitcombe family law attorney from The Law Offices of Daniel R. Ashford, P.A. will provide experienced and dedicated legal counsel to assist in resolving all matters involved in the dissolution of a marriage, and we will stand firm in negotiating those matters that concern most.</p>
  <p>Our goal as your attorney is to avoid making a bad situation worse; we fight for the right solutions for your family quickly and effectively. We understand the intricate balance of working towards your goals in the divorce while avoiding further conflict with your spouse.</p>
  <p>Our firm’s team has experience handling family law cases including divorce and legal separation. In cases of contested or uncontested divorce, mediation is often needed to negotiate to the terms and conditions of your split. This often means determining alimony, palimony, child custody and child support issues. Our lawyers are skilled mediators in divorce law, and we can help you tackle any of these issues. Sometimes the decision for joint custody does not end up working out and modification of child support and custody agreements is required. Furthermore, many splitting couples will need to determine how to divide their assets and property. This is often made easier with a prenuptial agreement or postnuptial agreement; however, whether or not this type of agreement exists a lawyer will still be needed for assistance.</p>
  <p>There are many more issues that may prompt a person to seek legal aide. For example, after a divorce has been finalized the support, visitation and/or relocation agreements verified at the time of the split may need spousal support modification to fit the new lifestyles of parents and children. Furthermore, grandparents often wish to protect the rights they have in regards to their grandchildren; these rights are equally as important as a mother’s rights or a father’s rights.</p>
  <span class="more">Read more</span>
</main>

<section class="widget" style="top:333px">
  <div class="tab">Video Center</div>
  <div class="body">
    <div class="row">
      <svg class="icon" viewBox="0 0 60 50"><rect x="1" y="4" width="58" height="40" rx="2" fill="#2b2b2b"/><rect x="4" y="7" width="52" height="30" fill="#4a4a4a"/><path d="M25 14L37 22L25 30Z" fill="#fff"/><rect x="4" y="39" width="52" height="2" fill="#999"/></svg>
      <p class="blurb"><b>Need more information?</b>Learn more about your case from our informative videos.</p>
    </div>
    <span class="click">Click Here »</span>
  </div>
</section>

<section class="widget" style="top:502px">
  <div class="tab">Click to Call</div>
  <div class="body">
    <div class="row">
      <svg class="icon" viewBox="0 0 60 70" style="height:70px"><rect x="14" y="4" width="32" height="62" rx="6" fill="#222"/><rect x="17" y="12" width="26" height="44" fill="#4b7fb1"/><circle cx="30" cy="61" r="2" fill="#666"/></svg>
      <p class="blurb">Have a question about your case? Click here to connect to our office.</p>
    </div>
    <span class="click">Click Here »</span>
  </div>
</section>

<section class="widget" style="top:671px">
  <div class="tab">Case Evaluation</div>
  <div class="body">
    <div class="row">
      <svg class="icon" viewBox="0 0 60 60"><rect x="10" y="4" width="40" height="52" fill="#f4f4f0" stroke="#bbb"/><g stroke="#aaa"><line x1="15" y1="14" x2="45" y2="14"/><line x1="15" y1="20" x2="45" y2="20"/><line x1="15" y1="26" x2="45" y2="26"/><line x1="15" y1="32" x2="40" y2="32"/></g><line x1="22" y1="48" x2="50" y2="36" stroke="#888" stroke-width="2"/></svg>
      <p class="blurb">Fill out our online case evaluation form to receive a free consultation.</p>
    </div>
    <span class="click">Click Here »</span>
  </div>
</section>

<section class="widget" style="top:831px">
  <div class="tab">Testimonials</div>
  <div class="body" style="height:100px">
    <p class="quote">This is very helpful website for us. Thanks for this</p>
    <span class="author">- Tavin</span>
    <div class="arrows">‹›</div>
  </div>
</section>

<footer class="footer">
  <p class="copy">© 2012<br>All Rights Reserved.</p>
  <div class="pay">
    <h3>We proudly accept :</h3>
    <div class="cards"><span class="card">Crestpay</span><span class="card">Vantacard</span><span class="card">Meridian</span><span class="card">Northstar</span></div>
  </div>
  <p class="links">Divorce Attorney | Contact Us | Resources | Privacy Policy | Site Map</p>
  <p class="legal">The information on this website is for general information purposes only. Nothing on this site should be taken as legal advice for any individual case or situation. This information is not intended to create, and receipt or viewing does not constitute, an attorney-client relationship.</p>
  <div class="badges"><span class="badge"></span><span class="badge round"></span><span class="badge"></span></div>
</footer>
</body>
</html>
```